Oven Cleaning flyer design

Hi there,
I need help designing a letterbox flyer. It needs to be DL size.
I have attached a rough design made with Chat GPT.
Would like back and front, have my business colors.
Please find attached mock up of what I would roughly like.
Also find attached logo.
Thank you

Target Market(s)

Home owners over 40

Industry/Entity Type

Cleaning

Requirements
Must have
• Logo, before after of oven, brand colors

```html
<!DOCTYPE html>
<html lang="en">
<head>
<meta charset="utf-8">
<title>Gleamwell Ovens – DL Flyer</title>
<link href="https://fonts.googleapis.com/css2?family=Poppins:wght@400;500;600;700;800&display=swap" rel="stylesheet">
<style>
:root{
  --teal:#45c1c9;
  --ink:#0b0b0b;
  --white:#ffffff;
  --stage:#808080;
  --text:#2b2b2b;
  --mist:#eef8fa;
}
*{box-sizing:border-box;margin:0;padding:0}
html,body{width:1200px;height:1191px;overflow:hidden}
body{background:var(--stage);font-family:'Poppins',sans-serif;position:relative;color:var(--ink)}
.flyer{position:absolute;top:175px;width:403px;height:855px;background:var(--white);overflow:hidden;box-shadow:6px 10px 18px rgba(0,0,0,.35)}
.flyer--front{left:139px}
.flyer--back{left:664px}
.brand{position:absolute;top:0;left:0;width:100%;height:100px;display:flex;align-items:center;justify-content:center;gap:10px}
.brand__dot{width:34px;height:34px;border-radius:50%;background:var(--teal)}
.brand__name{font-weight:700;font-size:22px;letter-spacing:1px;color:var(--ink);text-transform:uppercase}
.abs{position:absolute;left:0;top:0}
.hero-photo{position:absolute;left:0;top:100px;width:403px;height:330px}
.headline{position:absolute;left:0;top:462px;width:100%;text-align:center;font-weight:600;font-size:50px;line-height:46px;letter-spacing:-.5px}
.headline .accent{color:var(--teal)}
.intro{position:absolute;left:40px;top:626px;width:323px;text-align:center;font-size:13.6px;line-height:18.3px;color:var(--text)}
.contact-band{position:absolute;left:0;top:738px;width:100%;height:117px;background:var(--ink)}
.cta-pill{position:absolute;left:41px;top:720px;width:321px;height:30px;border-radius:15px;background:var(--teal);color:var(--white);font-weight:600;font-size:14.6px;display:flex;align-items:center;justify-content:center}
.phone{position:absolute;left:0;top:757px;width:100%;display:flex;align-items:center;justify-content:center;gap:10px;color:var(--white);font-weight:700;font-size:44px;line-height:50px;letter-spacing:-.5px}
.phone__icon{width:36px;height:36px;border-radius:50%;background:var(--teal);display:flex;align-items:center;justify-content:center}
.web{position:absolute;left:0;top:805px;width:100%;text-align:center;color:var(--teal);font-size:16.5px;letter-spacing:1.6px}
.services-bg{position:absolute;left:0;top:100px;width:403px;height:290px}
.services-title{position:absolute;left:99px;top:130px;width:205px;height:36px;background:var(--ink);color:var(--white);font-weight:600;font-size:26px;display:flex;align-items:center;justify-content:center;box-shadow:0 6px 8px rgba(0,0,0,.25)}
.service{position:absolute;top:201px;width:96px;margin-left:-48px;text-align:center;font-size:14px;line-height:14px}
.service__ring{width:48px;height:48px;margin:0 auto 9px;border-radius:50%;border:1.5px solid var(--ink);display:flex;align-items:center;justify-content:center;box-shadow:2px 0 0 var(--white)}
.service b{display:block;font-weight:700}
.seal{position:absolute;left:274px;top:306px;width:100px;height:100px}
.why{position:absolute;left:29px;top:412px;font-weight:600;font-size:29px;line-height:27px}
.why span{display:block;color:var(--teal)}
.about{position:absolute;left:29px;top:486px;width:350px;font-size:12.2px;line-height:18px;color:var(--text)}
.benefits{position:absolute;left:30px;top:595px;list-style:none}
.benefits li{display:flex;align-items:center;gap:10px;font-size:13.6px;line-height:13px;height:34px;margin-bottom:1px}
.tick{width:19px;height:19px;border-radius:50%;background:var(--teal);flex:none;display:flex;align-items:center;justify-content:center}
.coupon{position:absolute;left:209px;top:591px;width:158px;height:109px;border:1.3px dashed #555;border-radius:6px;text-align:center;padding-top:10px}
.coupon__off{font-weight:800;font-size:31px;line-height:30px}
.coupon__first{font-weight:800;font-size:20px;line-height:20px;color:var(--teal)}
.coupon__clean{font-weight:800;font-size:31px;line-height:28px;color:var(--teal)}
.coupon__note{font-size:9px;margin-top:3px}
.coupon__cut{position:absolute;left:66px;top:-9px;background:var(--white);padding:0 3px;font-size:12px;line-height:16px;color:#555}
</style>
</head>
<body>

<section class="flyer flyer--front">
  <header class="brand"><span class="brand__dot"></span><span class="brand__name">Gleamwell Ovens</span></header>
  <svg class="abs" width="403" height="110" style="top:98px" aria-hidden="true"><rect x="0" y="2" width="403" height="6" fill="var(--teal)"/></svg>
  <svg class="hero-photo" width="403" height="330" viewBox="0 0 403 330" role="img" aria-label="Before and after photo of an oven interior: grimy left half, clean right half">
    <defs>
      <linearGradient id="ovenTone" x1="0" x2="1">
        <stop offset="0" stop-color="#4a3a2a"/><stop offset=".49" stop-color="#2e2721"/>
        <stop offset=".51" stop-color="#2d3338"/><stop offset="1" stop-color="#4b5358"/>
      </linearGradient>
    </defs>
    <rect x="0" y="6" width="403" height="324" fill="url(#ovenTone)"/>
    <rect x="199" y="6" width="6" height="324" fill="var(--white)"/>
    <path d="M0 279 C60 265 120 272 200 292 S330 318 403 300 V330 H0Z" fill="var(--teal)"/>
    <path d="M0 300 C60 285 120 292 200 312 S330 332 403 316 V330 H0Z" fill="var(--white)"/>
  </svg>
  <h1 class="headline">Bring<br>Your <span class="accent">Oven</span><br>Back To Life</h1>
  <p class="intro">Professional, non-caustic oven cleaning that removes built-up grease, smoke, and burnt grime&nbsp; leaving your oven looking fresh again.</p>
  <div class="contact-band"></div>
  <div class="cta-pill">Call Now for Fast, Professional Service</div>
  <div class="phone"><span class="phone__icon"><svg width="18" height="18" viewBox="0 0 24 24"><path d="M6.6 10.8a15 15 0 0 0 6.6 6.6l2.2-2.2c.3-.3.7-.4 1-.2 1.1.4 2.3.6 3.6.6.6 0 1 .4 1 1V20c0 .6-.4 1-1 1A17 17 0 0 1 3 4c0-.6.4-1 1-1h3.5c.6 0 1 .4 1 1 0 1.3.2 2.5.6 3.6.1.3 0 .7-.2 1z" fill="var(--white)"/></svg></span>0400 628 915</div>
  <div class="web">www.gleamwellovens.com.au</div>
</section>

<section class="flyer flyer--back">
  <header class="brand"><span class="brand__dot"></span><span class="brand__name">Gleamwell Ovens</span></header>
  <svg class="services-bg" width="403" height="760" viewBox="0 0 403 760" aria-hidden="true" style="height:760px">
    <defs>
      <linearGradient id="mistFade" x1="0" y1="0" x2="0" y2="1">
        <stop offset="0" stop-color="var(--mist)"/><stop offset=".45" stop-color="var(--white)"/>
      </linearGradient>
    </defs>
    <rect x="0" y="0" width="403" height="760" fill="url(#mistFade)"/>
    <path d="M0 0 H403 V230 C330 236 270 248 200 262 S60 276 0 256 Z" fill="var(--teal)"/>
    <path d="M0 256 C60 276 130 276 200 262 S330 232 403 226 V238 C330 244 270 258 200 272 S60 286 0 262 Z" fill="var(--ink)"/>
  </svg>
  <h2 class="services-title">Our Services</h2>

  <div class="service" style="left:61px"><div class="service__ring"><svg width="24" height="24" viewBox="0 0 24 24" fill="none" stroke="var(--ink)" stroke-width="1.6"><rect x="3" y="3" width="18" height="18" rx="1.5"/><line x1="3" y1="8" x2="21" y2="8"/><rect x="6" y="11" width="12" height="7"/></svg></div><b>Oven</b>Cleaning</div>
  <div class="service" style="left:149px"><div class="service__ring"><svg width="26" height="24" viewBox="0 0 26 24" fill="none" stroke="var(--ink)" stroke-width="1.6"><rect x="2" y="7" width="22" height="11" rx="1.5"/><circle cx="8" cy="12" r="3"/><circle cx="18" cy="12" r="3"/></svg></div><b>Cooktop</b>Cleaning</div>
  <div class="service" style="left:245px"><div class="service__ring"><svg width="26" height="24" viewBox="0 0 26 24" fill="none" stroke="var(--ink)" stroke-width="1.6"><rect x="11" y="2" width="4" height="8"/><path d="M3 18 L10 10 H16 L23 18 Z"/><line x1="3" y1="21" x2="23" y2="21"/></svg></div><b>Rangehood</b>Cleaning</div>
  <div class="service" style="left:343px"><div class="service__ring"><svg width="24" height="24" viewBox="0 0 24 24" fill="none" stroke="var(--ink)" stroke-width="1.6"><line x1="3" y1="9" x2="21" y2="9"/><path d="M5 11 Q12 18 19 11"/><line x1="8" y1="15" x2="6" y2="21"/><line x1="16" y1="15" x2="18" y2="21"/><line x1="12" y1="16" x2="12" y2="21"/></svg></div><b>BBQ</b>Cleaning</div>

  <svg class="seal" viewBox="0 0 100 100" role="img" aria-label="Satisfaction guarantee seal">
    <circle cx="50" cy="50" r="49" fill="var(--ink)"/>
    <circle cx="50" cy="50" r="38" fill="none" stroke="var(--teal)" stroke-width="6"/>
  </svg>

  <h2 class="why">Why Choose<span>Gleamwell Ovens?</span></h2>
  <p class="about">We're a local family business providing professional, non-caustic oven cleaning across Sunshine Coast. Using specialized equipment and proven cleaning methods, we remove heavy grease, carbon build-up, smoke residue, restoring your oven safely and effectively.</p>

  <ul class="benefits">
    <li><span class="tick"><svg width="11" height="11" viewBox="0 0 12 12"><path d="M2 6.5 L5 9 L10 3" fill="none" stroke="var(--white)" stroke-width="2"/></svg></span>Reliable<br>Service</li>
    <li><span class="tick"><svg width="11" height="11" viewBox="0 0 12 12"><path d="M2 6.5 L5 9 L10 3" fill="none" stroke="var(--white)" stroke-width="2"/></svg></span>Non-Caustic<br>Cleaning</li>
    <li><span class="tick"><svg width="11" height="11" viewBox="0 0 12 12"><path d="M2 6.5 L5 9 L10 3" fill="none" stroke="var(--white)" stroke-width="2"/></svg></span>Satisfaction<br>Guaranteed</li>
  </ul>

  <div class="coupon">
    <span class="coupon__cut">&#9986;</span>
    <div class="coupon__off">$10 OFF</div>
    <div class="coupon__first">YOUR FIRST</div>
    <div class="coupon__clean">CLEAN</div>
    <div class="coupon__note">When You Mention this flyer</div>
  </div>

  <div class="contact-band"></div>
  <div class="cta-pill">Call Now for Fast, Professional Service</div>
  <div class="phone"><span class="phone__icon"><svg width="18" height="18" viewBox="0 0 24 24"><path d="M6.6 10.8a15 15 0 0 0 6.6 6.6l2.2-2.2c.3-.3.7-.4 1-.2 1.1.4 2.3.6 3.6.6.6 0 1 .4 1 1V20c0 .6-.4 1-1 1A17 17 0 0 1 3 4c0-.6.4-1 1-1h3.5c.6 0 1 .4 1 1 0 1.3.2 2.5.6 3.6.1.3 0 .7-.2 1z" fill="var(--white)"/></svg></span>0400 628 915</div>
  <div class="web">www.gleamwellovens.com.au</div>
</section>

</body>
</html>
```